Simple proffessional BC

I have a logo which I will attach below.
I would like the logo on the front of the card with these details in point form below:
Pre and Post Natal Yoga: Pregnancy Workshops: Hypnobirthing Courses
On the back of the card my details:
Marla Pennick
Facebook page- stretchbelliesbayridgefield
Mobile- 0491 352 718

I like the idea of the card being simple, possibly just the above on a plain coloured (eggshell?) card, a card that is textured.
I am open to suggestion if it appeals!
Thank you and good luck!

Target Market(s)

Pregnant women, 20's-40's

Requirements
Must have
• Simple, compliment logo.
Make logo the feature.
Should not have

• .

```html
<!DOCTYPE html>
<html lang="en">
<head>
<meta charset="utf-8">
<title>Stretch Bellies – Business Card</title>
<link rel="stylesheet" href="https://fonts.googleapis.com/css2?family=Questrial&display=swap">
<style>
  :root {
    --maroon: #62100f;
    --saffron: #e9a23b;
    --paper: #ffffff;
    --backdrop: #eee7da;
    --ink: #6a1513;
  }
  * { margin: 0; padding: 0; box-sizing: border-box; }
  html, body {
    width: 1200px; height: 1000px; overflow: hidden;
    background: var(--backdrop);
    font-family: "Questrial", "Century Gothic", sans-serif;
  }
  .sheet {
    position: relative; width: 1200px; height: 1000px;
    display: flex; align-items: center; justify-content: center; gap: 60px;
  }
  .card {
    position: relative; width: 540px; height: 330px;
    box-shadow: 0 6px 18px rgba(60, 30, 10, 0.18);
  }
  /* Front */
  .card--front { background: var(--maroon); }
  .front__mark {
    position: absolute; left: 50%; top: 44px; transform: translateX(-50%);
    display: flex; flex-direction: column; align-items: center; gap: 18px;
  }
  .front__circle {
    width: 150px; height: 150px; border-radius: 50%; background: var(--saffron);
  }
  .front__name { color: var(--saffron); font-size: 30px; letter-spacing: 1px; }
  .front__services {
    position: absolute; right: 22px; bottom: 18px;
    color: var(--saffron); font-size: 11.5px; letter-spacing: 0.3px;
  }
  /* Back */
  .card--back { background: var(--paper); border-left: 8px solid var(--maroon); }
  .back__brand {
    position: absolute; left: 34px; top: 34px;
    display: flex; align-items: center; gap: 16px;
  }
  .back__circle { width: 58px; height: 58px; border-radius: 50%; background: var(--saffron); }
  .back__name-brand { color: var(--ink); font-size: 36px; }
  .back__person {
    position: absolute; left: 110px; top: 140px;
    color: var(--ink); font-size: 26px;
  }
  .back__contact {
    position: absolute; left: 34px; top: 210px;
    color: var(--ink); font-size: 21px; line-height: 1.45;
  }
  .contact__row { display: flex; align-items: center; gap: 8px; }
  .contact__icon { width: 14px; height: 20px; flex: none; }
</style>
</head>
<body>
<main class="sheet">
  <section class="card card--front" aria-label="Card front">
    <div class="front__mark">
      <div class="front__circle"></div>
      <div class="front__name">Stretch Bellies</div>
    </div>
    <p class="front__services">Pre and Post Natal Yoga | Pregnancy Workshops | Hypnobirthing Courses</p>
  </section>

  <section class="card card--back" aria-label="Card back">
    <div class="back__brand">
      <div class="back__circle"></div>
      <div class="back__name-brand">Stretch Bellies</div>
    </div>
    <p class="back__person">Marla Pennick</p>
    <div class="back__contact">
      <div class="contact__row">
        <svg class="contact__icon" viewBox="0 0 14 20" aria-hidden="true">
          <rect x="1" y="1" width="12" height="18" rx="2" fill="none" stroke="#e9a23b" stroke-width="1.6"/>
          <line x1="5" y1="16" x2="9" y2="16" stroke="#e9a23b" stroke-width="1.4"/>
        </svg>
        <span>0491 352 718</span>
      </div>
      <div class="contact__row"><span>stretchbelliesbayridgefield</span></div>
    </div>
  </section>
</main>
</body>
</html>
```